Roofing web site brvt roofing

Look at some of our competitors web page we like something similar with NYC roofing
https://www.quillbarroofing.example/
Maybe a skyline picture of nyc at the home page with a picture of flat roofing installation

Target Market(s)

Commercial and residential flat roofs

Industry/Entity Type

Flat Roofing industry

Coding

Coded - Design and coding required

Number of Pages Required

2 page

Font styles to use
Decorative
Script

Colors

Designer to choose colors to be used in the design.

Requirements
Must have
• At BRVT Roofing, we are a trusted and reputable roofing company specializing in new construction flat roof installation and repair. With years of experience in the industry, we take pride in providing exceptional roofing solutions to our valued clients. Our team of highly skilled and dedicated roofing professionals understands the unique challenges and requirements of new construction projects. We work closely with builders, contractors, and architects to design and install flat roofs that meet the specific needs of each project. From commercial buildings to residential complexes, we have the expertise to deliver reliable and durable roofing solutions. When it comes to flat roof repairs, we are your go-to experts. Our experienced technicians conduct thorough inspections to identify the root cause of any issues your roof may be experiencing. We utilize the latest industry techniques and high-quality materials to efficiently repair your flat roof, ensuring its integrity and longevity. At BRVT Roofing, we prioritize customer satisfaction above all else. We believe in building strong relationships with our clients by providing exceptional craftsmanship and outstanding customer service. Our team is dedicated to delivering projects on time, within budget, and to the highest standards of quality. We understand that a well-maintained roof is essential for protecting your property and ensuring the safety of its occupants. That's why we use only the best materials and employ skilled professionals who are trained in the latest roofing practices. Our commitment to excellence is evident in every project we undertake. As a fully licensed and insured roofing company, we prioritize safety and adhere to industry regulations and best practices. We take every precaution to create a safe working environment for our team and minimize any disruptions to your daily routine. When you choose BRVT Roofing, you can trust that you are working with a reliable and reputable company that will deliver exceptional results. We are committed to exceeding your expectations and providing you with a roof that is built to last. Contact us today for all your new construction flat roof installation and repair needs.
Nice to have
• NYC skyline background with commercial roofing pictures of torching roofing

```html
<!DOCTYPE html>
<html lang="en">
<head>
<meta charset="utf-8">
<title>BRVT Roofing</title>
<link href="https://fonts.googleapis.com/css2?family=Poppins:ital,wght@0,300;0,400;0,500;0,600;0,700;1,400&display=swap" rel="stylesheet">
<style>
:root{
  --orange:#ef5f2a;
  --orange-deep:#d65220;
  --ink:#2b2b2b;
  --text:#5a5a5a;
  --muted:#7a7a7a;
  --light:#f5f5f5;
  --white:#ffffff;
  --line:#e2e2e2;
}
*{box-sizing:border-box;margin:0;padding:0}
html,body{width:1200px;height:4831px;overflow:hidden}
body{font-family:'Poppins',sans-serif;color:var(--text);background:var(--white);position:relative}
.abs{position:absolute}
a{color:inherit;text-decoration:none}

/* header */
.topbar{left:600px;top:0;width:600px;height:58px;background:var(--orange);border-bottom-left-radius:58px;display:flex;align-items:center;justify-content:center;gap:34px;color:var(--white);font-size:15px}
.topbar span{display:flex;align-items:center;gap:10px}
.header{left:0;top:0;width:1200px;height:171px}
.logo{left:88px;top:36px;width:200px;height:200px;border-radius:50%;background:var(--white);box-shadow:0 4px 14px rgba(0,0,0,.15);display:flex;align-items:center;justify-content:center;z-index:3}
.logo-inner{width:178px;height:178px;border-radius:50%;background:var(--orange);display:flex;align-items:center;justify-content:center;color:var(--white);font-weight:700;font-size:24px;letter-spacing:1px}
.nav{left:490px;top:103px;display:flex;gap:22px;font-size:15px;color:#444}
.nav .active{color:var(--orange);border-bottom:2px solid var(--orange);padding-bottom:3px}
.btn{display:inline-flex;align-items:center;justify-content:center;font-size:17px;color:var(--white)}
.btn-fill{background:var(--orange)}
.btn-line{border:2px solid var(--white)}
.contact-btn{left:981px;top:94px;width:137px;height:43px;font-size:15px}

/* hero */
.hero{left:0;top:171px;width:1200px;height:753px;background:linear-gradient(100deg,#3c4650 0%,#56636b 45%,#6f7a72 70%,#4f5a4c 100%)}
.hero-shade{inset:0;background:linear-gradient(90deg,rgba(20,24,30,.55),rgba(20,24,30,.1))}
.hero h1{left:82px;top:255px;font-size:60px;font-weight:600;color:var(--white);line-height:1}
.hero p{left:82px;top:337px;width:620px;font-size:15px;line-height:26px;color:#f1f1f1}
.hero .b1{left:84px;top:435px;width:162px;height:52px}
.hero .b2{left:264px;top:435px;width:162px;height:52px}

.thumb{width:338px;height:202px;top:844px;background:var(--white);border-radius:60px 0 40px 0;box-shadow:0 6px 16px rgba(0,0,0,.18);padding:10px}
.thumb div{width:100%;height:100%;border-radius:52px 0 34px 0}

/* about */
.about-img{left:86px;top:1172px;width:300px;height:400px;border-radius:0 110px 0 0;background:linear-gradient(140deg,#0e1a2e,#22395a 45%,#8a4a1e 80%,#c9702a)}
.about-circle{left:276px;top:1414px;width:216px;height:216px;border-radius:50%;border:6px solid var(--white);background:linear-gradient(160deg,#8fb3d4,#6f8a9c 50%,#5a4a3a)}
.about h2{left:527px;top:1172px;font-size:60px;font-weight:600;color:var(--orange)}
.about h3{left:527px;top:1250px;font-size:16px;font-weight:600;color:#333}
.about p{left:527px;width:570px;font-size:15px;line-height:26px;color:var(--text)}
.about .btn{left:527px;top:1547px;width:161px;height:51px}

/* services */
.services{left:0;top:1702px;width:1200px;height:767px;background:var(--light)}
.sec-title{width:1200px;text-align:center;font-size:58px;font-weight:600;color:var(--orange);left:0}
.svc{width:323px;height:449px;top:165px;background:var(--white);border:1px solid var(--line);padding:11px;text-align:center}
.svc.raised{box-shadow:0 8px 18px rgba(0,0,0,.14);border-color:transparent}
.svc .pic{height:197px;border-radius:6px}
.svc h4{margin-top:46px;font-size:17px;font-weight:500;color:var(--orange)}
.svc p{margin:10px auto 0;width:285px;font-size:13.5px;line-height:22px;color:var(--text)}
.svc .more{display:inline-flex;align-items:center;gap:8px;margin-top:18px;font-size:14px;color:var(--orange)}
.arrow{width:56px;height:56px;border-radius:50%;background:var(--orange);top:651px;display:flex;align-items:center;justify-content:center}

/* cta */
.cta{left:0;top:2469px;width:1200px;height:375px;background:linear-gradient(120deg,var(--orange-deep),#e2622a 50%,#c84a17);text-align:center;color:var(--white)}
.cta h2{top:92px;left:0;width:1200px;font-size:40px;font-weight:500}
.cta p{top:160px;left:190px;width:820px;font-size:18px;line-height:25px}
.cta .btn{left:525px;top:231px;width:161px;height:51px}

/* portfolio */
.portfolio{left:0;top:2844px;width:1200px;height:962px;background:var(--light)}
.portfolio .lead{left:180px;top:172px;width:840px;text-align:center;font-size:15px;line-height:26px;color:var(--text)}
.tile{position:absolute}
.tile-feature{left:81px;top:268px;width:693px;height:300px;background:linear-gradient(180deg,#9a4a22,#7a3a1c);color:var(--white);text-align:center;padding:88px 40px 0}
.tile-feature h4{font-size:19px;font-weight:400}
.tile-feature p{margin-top:12px;font-size:14.5px;line-height:22px}

/* testimonials */
.testi{left:0;top:3806px;width:1200px;height:535px;background:var(--white)}
.card{top:178px;width:337px;height:257px;background:#f7f7f7;box-shadow:0 2px 8px rgba(0,0,0,.06);padding:32px 30px}
.stars{color:#f5a12a;font-size:25px;letter-spacing:2px}
.badge{position:absolute;right:32px;top:30px;width:36px;height:36px;border-radius:50%;background:#e4e4e4}
.card p{margin-top:16px;font-size:13px;line-height:21px;color:var(--muted);width:270px}
.person{display:flex;align-items:center;gap:16px;margin-top:22px}
.avatar{width:68px;height:68px;border-radius:50%;background:linear-gradient(140deg,#c9a07a,#6b4a3a)}
.person b{display:block;font-weight:400;font-size:18px;color:#333}
.person i{font-size:15px;color:var(--orange);font-weight:500}

/* footer */
.footer{left:0;top:4341px;width:1200px;height:490px;background:linear-gradient(120deg,var(--orange-deep),#e0602a 50%,#c94c18);color:var(--white)}
.fcol{top:118px}
.fcol h5{font-size:19px;font-weight:400;padding-bottom:10px;position:relative}
.fcol h5 b{font-weight:600}
.fcol h5::after{content:"";position:absolute;left:0;bottom:0;width:38px;height:2px;background:var(--white)}
.fcol ul{list-style:none;margin-top:24px}
.fcol li{font-size:15px;line-height:31px;padding-left:8px}
.fcol li::before{content:"›";margin-right:12px}
.news p{margin-top:22px;font-size:15px;line-height:20px;width:260px}
.news .field{margin-top:28px;width:250px;height:35px;background:var(--white)}
.news .sub{margin-top:15px;width:126px;height:34px;background:var(--white);color:#333;font-size:12px;display:flex;align-items:center;justify-content:center}
.divider{left:0;top:369px;width:1200px;height:1px;background:rgba(255,255,255,.5)}
.copy{left:88px;top:418px;font-size:17px}
.social{left:912px;top:409px;display:flex;gap:11px}
.social span{width:41px;height:41px;border-radius:50%;border:2px solid var(--white);display:flex;align-items:center;justify-content:center}
.social span i{width:14px;height:14px;border-radius:50%;background:var(--white)}
</style>
</head>
<body>

<header class="abs header">
  <div class="abs topbar">
    <span>
      <svg width="24" height="24" viewBox="0 0 24 24" fill="none" stroke="#fff" stroke-width="1.6"><circle cx="12" cy="12" r="11"/><path d="M8.5 7c.6-.6 1.4-.5 1.7.2l.7 1.6c.2.5 0 1-.4 1.3l-.6.4c.5 1.4 1.6 2.6 3 3.1l.4-.6c.3-.4.9-.6 1.300-.4l1.6.7c.7.3.8 1.1.2 1.7-1 1-2.6 1.2-4 .4-2-1.1-3.600-2.7-4.600-4.700-.7-1.300-.5-2.800.7-3.700z"/></svg>
      555-014-2290
    </span>
    <span>
      <svg width="24" height="24" viewBox="0 0 24 24" fill="none" stroke="#fff" stroke-width="1.6"><circle cx="12" cy="12" r="11"/><path d="M12 18s-4.5-4.3-4.5-7.5a4.5 4.5 0 0 1 9 0C16.5 13.7 12 18 12 18z"/><circle cx="12" cy="10.5" r="1.6"/></svg>
      The dummy &nbsp;Address
    </span>
  </div>
  <div class="abs logo"><div class="logo-inner">BRVT</div></div>
  <nav class="abs nav">
    <a class="active">Home</a><a>About us</a><a>What We do</a><a>Our Blogs</a><a>Testimonials</a>
  </nav>
  <a class="abs btn btn-fill contact-btn">Contact Us</a>
</header>

<section class="abs hero">
  <div class="abs hero-shade" role="img" aria-label="Roofer torching a flat roof membrane with the city skyline behind"></div>
  <h1 class="abs">BRVT ROOFING</h1>
  <p class="abs">New construction flat roof installation and repair. We work closely with builders, contractors and architects to design and install flat roofs built to last.</p>
  <a class="abs btn btn-fill b1">Read More</a>
  <a class="abs btn btn-line b2">Read More</a>
</section>

<div class="abs thumb" style="left:79px"><div role="img" aria-label="Roofer working on a commercial flat roof" style="background:linear-gradient(160deg,#8aa6c2,#b9a6b4 45%,#5fb7a6)"></div></div>
<div class="abs thumb" style="left:431px"><div role="img" aria-label="Technician preparing roofing materials" style="background:linear-gradient(160deg,#3a3a3a,#6d6a66 50%,#2a2a2a)"></div></div>
<div class="abs thumb" style="left:784px"><div role="img" aria-label="Crew installing a new roof on a residential building" style="background:linear-gradient(160deg,#9b8270,#6e5644 50%,#c7a15c)"></div></div>

<section class="about">
  <div class="abs about-img" role="img" aria-label="Torch applied roofing membrane with sparks"></div>
  <div class="abs about-circle" role="img" aria-label="Roofer kneeling on a rooftop"></div>
  <h2 class="abs">ABOUT US</h2>
  <h3 class="abs">NEW CONSTRUCTION FLAT ROOF SPECIALISTS</h3>
  <p class="abs" style="top:1300px">At BRVT Roofing, we are a trusted and reputable roofing company specializing in new construction flat roof installation and repair. With years of experience in the industry, we take pride in providing exceptional roofing solutions to our valued clients.</p>
  <p class="abs" style="top:1454px">From commercial buildings to residential complexes, we have the expertise to deliver reliable and durable roofing solutions.</p>
  <a class="abs btn btn-fill">Read More</a>
</section>

<section class="abs services">
  <h2 class="abs sec-title" style="top:58px">OUR SERVICES</h2>
  <div class="abs svc" style="left:105px">
    <div class="pic" role="img" aria-label="Roofer in hard hat on a roof" style="background:linear-gradient(150deg,#8d8d86,#5d6157 50%,#c7d23a)"></div>
    <h4>FLAT ROOF INSTALLATION</h4>
    <p>New construction flat roofs designed and installed to meet the specific needs of each project.</p>
  </div>
  <div class="abs svc raised" style="left:442px">
    <div class="pic" role="img" aria-label="Commercial roof structure seen from below" style="background:linear-gradient(180deg,#b7c4cf,#e7ecf0 50%,#9aa9b5)"></div>
    <h4>FLAT ROOF REPAIRS</h4>
    <p>Thorough inspections find the root cause, then quality materials restore your roof's integrity.</p>
    <a class="more">READ MORE
      <svg width="17" height="17" viewBox="0 0 17 17" fill="none" stroke="#ef5f2a" stroke-width="1.5"><circle cx="8.5" cy="8.5" r="7.5"/><path d="M6 8.5h5M9 6l2.5 2.5L9 11"/></svg>
    </a>
  </div>
  <div class="abs svc" style="left:778px">
    <div class="pic" role="img" aria-label="Residential building under construction with scaffolding" style="background:linear-gradient(170deg,#7fa6d6,#c9b593 55%,#8a6a4a)"></div>
    <h4>LICENSED &amp; INSURED</h4>
    <p>We follow industry regulations and best practices to keep every job site safe and tidy.</p>
  </div>
  <span class="abs arrow" style="left:538px"><svg width="16" height="16" viewBox="0 0 16 16" fill="none" stroke="#fff" stroke-width="2.2"><path d="M10 3L5 8l5 5"/></svg></span>
  <span class="abs arrow" style="left:608px"><svg width="16" height="16" viewBox="0 0 16 16" fill="none" stroke="#fff" stroke-width="2.2"><path d="M6 3l5 5-5 5"/></svg></span>
</section>

<section class="abs cta">
  <h2 class="abs">ARE YOU READY TO START A CONVERSATION</h2>
  <p class="abs">Contact us today for all your new construction flat roof installation and repair needs. We deliver on time and within budget.</p>
  <a class="abs btn btn-line" style="border-width:1px">Contact Us</a>
</section>

<section class="abs portfolio">
  <h2 class="abs sec-title" style="top:90px">OUR PORTFOLIO</h2>
  <p class="abs lead">Tailored to Your Needs. Discover how we can bring your vision to life, covering every aspect of construction from the initial design to the final touches.</p>
  <div class="tile tile-feature" role="img" aria-label="City skyline under an orange overlay">
    <h4>COMMERCIAL &amp; RESIDENTIAL FLAT ROOFS</h4>
    <p>Our team of highly skilled roofing professionals understands the unique challenges of new construction projects, delivering reliable, durable roofs with outstanding customer service.</p>
  </div>
  <div class="tile" role="img" aria-label="Commercial roof lattice from below" style="left:784px;top:268px;width:343px;height:642px;background:linear-gradient(150deg,#5c6f7f,#c7d0d6 45%,#8795a2)"></div>
  <div class="tile" role="img" aria-label="Roof surface in the rain" style="left:81px;top:578px;width:343px;height:328px;background:linear-gradient(180deg,#8f4a32,#6c3b2a 60%,#a8b0b4)"></div>
  <div class="tile" role="img" aria-label="Red house among autumn trees" style="left:433px;top:578px;width:341px;height:328px;background:linear-gradient(180deg,#b6cde0,#c9823a 45%,#7a2a22 70%,#6a7a3a)"></div>
</section>

<section class="abs testi">
  <h2 class="abs sec-title" style="top:72px">CLIENTS TESTIMONIALS</h2>
  <div class="abs card" style="left:68px">
    <span class="badge"></span>
    <div class="stars">★★★★★</div>
    <p>Our new building's flat roof went on fast, clean and on budget. The crew was a pleasure to work with.</p>
    <div class="person"><span class="avatar" role="img" aria-label="Client portrait"></span><div><b>Dara Wells</b><i>Organiser</i></div></div>
  </div>
  <div class="abs card" style="left:428px">
    <span class="badge"></span>
    <div class="stars">★★★★★</div>
    <p>They found the real cause of our roof leak and fixed it for good. Honest, skilled and on time.</p>
    <div class="person"><span class="avatar" role="img" aria-label="Client portrait"></span><div><b>Dara Wells</b><i>Organiser</i></div></div>
  </div>
  <div class="abs card" style="left:797px">
    <span class="badge"></span>
    <div class="stars">★★★★★</div>
    <p>Safe, tidy job site and great service from start to finish. A roof that is truly built to last.</p>
    <div class="person"><span class="avatar" role="img" aria-label="Client portrait" style="background:linear-gradient(140deg,#e0b53a,#5a4a3a)"></span><div><b>Dara Wells</b><i>Organiser</i></div></div>
  </div>
</section>

<footer class="abs footer">
  <div class="abs fcol" style="left:232px">
    <h5>Quick <b>Links</b></h5>
    <ul><li>Home</li><li>About Us</li><li>Our Gallery</li><li>Our Blogs</li><li>Testimonials</li></ul>
  </div>
  <div class="abs fcol" style="left:489px">
    <h5>Quick <b>Links</b></h5>
    <ul><li>Terms &nbsp;&amp; Condition</li><li>Privacy Policy</li><li>Support</li></ul>
  </div>
  <div class="abs fcol news" style="left:748px">
    <h5>Our <b>Newsletter</b></h5>
    <p>Subscribe our newsletter to get the latest news.</p>
    <div class="field"></div>
    <div class="sub">SUBSCRIBE</div>
  </div>
  <div class="abs divider"></div>
  <div class="abs copy">All Rights Reserved @ Copyrights 2023</div>
  <div class="abs social"><span><i></i></span><span><i></i></span><span><i></i></span><span><i></i></span></div>
</footer>

</body>
</html>
```